design a construction company business card

Design business card around our logo. Card must have all the typical info: name, title, address, phone, email, business name, etc. Somewhere on the card I would like to see our motto "Built on integrity... Inspired by commitment." Consider adding a splash of bright orange to the card to complement the blues and silvers/grays in the logo. We are open to metallic inks, textures, etc. We would like to see options on both light and dark backgrounds. The font in the logo is Euro Technic Extended Regular.

```html
<!DOCTYPE html>
<html lang="en">
<head>
<meta charset="utf-8">
<title>Halden Builders – Business Card</title>
<link href="https://fonts.googleapis.com/css2?family=Open+Sans:wght@400;600&display=swap" rel="stylesheet">
<style>
  :root {
    --stage-center: #e9eaeb;
    --stage-edge: #cdced0;
    --card-light: #ffffff;
    --card-dark: #808184;
    --brand-blue: #1f74c4;
    --brand-navy: #2a3796;
    --band-gray: #8a8b8e;
    --text-gray: #555659;
    --white: #ffffff;
  }
  * { box-sizing: border-box; margin: 0; padding: 0; }
  html, body { width: 800px; height: 1200px; overflow: hidden; }
  body {
    position: relative;
    font-family: "Open Sans", sans-serif;
    background: radial-gradient(ellipse at 50% 50%, var(--stage-center) 0%, var(--stage-edge) 100%);
    border: 1px solid #9a9b9d;
  }
  .card {
    position: absolute;
    left: 148px;
    width: 504px;
    height: 288px;
    overflow: hidden;
  }
  .card--front { top: 174px; background: var(--card-light); }
  .card--back { top: 703px; background: var(--card-dark); }

  .brand-name {
    position: absolute;
    left: 0; right: 0;
    text-align: center;
    font-weight: 600;
    font-size: 25px;
    letter-spacing: 0.5px;
  }
  .card--front .brand-name { top: 62px; color: var(--brand-blue); }
  .card--back .brand-name { top: 128px; color: var(--white); }

  .identity {
    position: absolute;
    right: 266px;
    top: 160px;
    text-align: right;
    color: var(--text-gray);
  }
  .identity__name {
    font-weight: 600;
    font-size: 22px;
    line-height: 26px;
    color: var(--brand-blue);
  }
  .identity__title { font-size: 12.5px; line-height: 16px; margin-bottom: 5px; }
  .identity__address { font-size: 12.5px; line-height: 17px; }

  .divider {
    position: absolute;
    left: 252px;
    top: 158px;
    width: 1px;
    height: 89px;
    background: var(--brand-blue);
  }

  .contacts {
    position: absolute;
    left: 268px;
    top: 167px;
    list-style: none;
    color: var(--text-gray);
    font-size: 12.5px;
  }
  .contacts li {
    display: flex;
    align-items: center;
    height: 18px;
  }
  .contacts svg { width: 10px; height: 10px; margin-right: 6px; flex: none; }

  .footer-bands { position: absolute; left: 0; bottom: 0; width: 504px; height: 26px; }
</style>
</head>
<body>

<section class="card card--front">
  <div class="brand-name">Halden Builders, Inc.</div>

  <div class="identity">
    <div class="identity__name">Daniel Marsh</div>
    <div class="identity__title">Managing Member</div>
    <div class="identity__address">2270 Ridgeline Ave,<br>Riverton, CA 95720</div>
  </div>

  <div class="divider"></div>

  <ul class="contacts">
    <li>
      <svg viewBox="0 0 10 10"><path d="M2 1 L4 3 L3 4 Q4 6 6 7 L7 6 L9 8 L8 9.5 Q3 9 0.5 2 Z" fill="var(--brand-blue)"/></svg>
      (916) 555-0142
    </li>
    <li>
      <svg viewBox="0 0 10 10"><rect x="2.5" y="0.5" width="5" height="9" rx="1" fill="none" stroke="var(--brand-blue)" stroke-width="1.2"/><circle cx="5" cy="8" r="0.6" fill="var(--brand-blue)"/></svg>
      (530) 555-0187
    </li>
    <li>
      <svg viewBox="0 0 10 10"><rect x="0.5" y="2" width="9" height="6" fill="var(--brand-blue)"/><path d="M0.5 2 L5 5.5 L9.5 2" fill="none" stroke="var(--white)" stroke-width="0.8"/></svg>
      daniel@haldenbuild.com
    </li>
    <li>
      <svg viewBox="0 0 10 10"><circle cx="5" cy="5" r="4.5" fill="var(--brand-blue)"/><path d="M0.5 5 H9.5 M5 0.5 V9.5 M5 0.5 Q2 5 5 9.5 M5 0.5 Q8 5 5 9.5" fill="none" stroke="var(--white)" stroke-width="0.6"/></svg>
      www.haldenbuild.com
    </li>
  </ul>

  <svg class="footer-bands" viewBox="0 0 504 26" aria-hidden="true">
    <defs>
      <linearGradient id="bandBlue" x1="0" x2="1" y1="0" y2="0">
        <stop offset="0" stop-color="var(--brand-navy)"/>
        <stop offset="1" stop-color="var(--brand-blue)"/>
      </linearGradient>
    </defs>
    <polygon points="0,3 312,3 305,9 0,9" fill="var(--band-gray)"/>
    <polygon points="324,0 504,0 504,26 0,26 0,14 308,14" fill="url(#bandBlue)"/>
  </svg>
</section>

<section class="card card--back">
  <div class="brand-name">Halden Builders, Inc.</div>
</section>

</body>
</html>
```